Business cards for KORU Real Estate Holdings LLC

We need a cool, original business card design for a company based in the Washington DC metropolitan area. We are a new energetic and passionate Real Estate Investing Company that invests in all types of real estate; commercial, residential, industrial etc.

Our company color is Red since it reflects action, energy and speed; it is assertive confident, energizing, exciting, powerful, passionate and determined. So we would like business card communicate those qualities to the audience.

Our audiences are investors that want to invest with us, real estate sellers, buyers, and tenants who lease from us.

Our logo is attached

```html
<!DOCTYPE html>
<html lang="en">
<head>
<meta charset="utf-8">
<title>KORU Real Estate Holdings LLC — Business Cards</title>
<link href="https://fonts.googleapis.com/css2?family=Exo+2:wght@400;600&display=swap" rel="stylesheet">
<style>
  :root {
    --backdrop: #e9e7e4;
    --card: #ffffff;
    --ink: #3a3a3c;
    --ink-soft: #4a4a4d;
    --brand-red: #d8686c;
  }
  html, body {
    margin: 0;
    width: 1200px;
    height: 903px;
    overflow: hidden;
    background: var(--backdrop);
    font-family: "Exo 2", sans-serif;
    color: var(--ink);
  }
  .card {
    position: absolute;
    left: 250px;
    width: 700px;
    height: 400px;
    background: var(--card);
    box-shadow: 0 6px 20px rgba(0,0,0,.12);
    overflow: hidden;
  }
  .card--brand { top: 30px; }
  .card--contact { top: 470px; }

  .wordmark {
    display: flex;
    align-items: center;
    gap: 12px;
    font-weight: 600;
    color: var(--ink);
  }
  .wordmark__square {
    width: 26px;
    height: 26px;
    background: var(--brand-red);
    flex: none;
  }
  .wordmark__name { display: flex; flex-direction: column; line-height: 1.05; }
  .wordmark__main { font-size: 52px; letter-spacing: 3px; }
  .wordmark__sub { font-size: 15px; letter-spacing: .5px; }

  .card--brand .wordmark {
    position: absolute;
    left: 50%;
    top: 50%;
    transform: translate(-50%, -50%);
  }

  .card--contact .wordmark {
    position: absolute;
    left: 200px;
    top: 62px;
    gap: 9px;
  }
  .card--contact .wordmark__square { width: 18px; height: 18px; }
  .card--contact .wordmark__main { font-size: 36px; letter-spacing: 2px; }
  .card--contact .wordmark__sub { font-size: 10.5px; }

  .band { position: absolute; background: var(--ink); }
  .band--top { left: 150px; top: 0; width: 70px; height: 22px; }
  .band--side { left: 440px; top: 150px; width: 260px; height: 26px; }

  .address {
    position: absolute;
    left: 40px;
    top: 198px;
    display: flex;
    gap: 10px;
    font-size: 14px;
    line-height: 1.45;
    color: var(--ink-soft);
  }
  .person {
    position: absolute;
    left: 360px;
    top: 190px;
  }
  .person__name { font-size: 19px; font-weight: 600; letter-spacing: 1.5px; margin: 0; }
  .person__role { font-size: 14px; margin: 2px 0 0; color: var(--ink-soft); }

  .contacts {
    position: absolute;
    left: 305px;
    top: 262px;
    margin: 0;
    padding: 0;
    list-style: none;
    font-size: 12.5px;
    color: var(--ink-soft);
  }
  .contacts li { display: flex; align-items: center; gap: 8px; height: 21px; }
  .icon { width: 12px; height: 12px; fill: var(--ink); flex: none; }
</style>
</head>
<body>

<section class="card card--brand">
  <div class="wordmark">
    <span class="wordmark__square"></span>
    <span class="wordmark__name">
      <span class="wordmark__main">KORU</span>
      <span class="wordmark__sub">REAL ESTATE HOLDINGS LLC</span>
    </span>
  </div>
</section>

<section class="card card--contact">
  <span class="band band--top"></span>
  <div class="wordmark">
    <span class="wordmark__square"></span>
    <span class="wordmark__name">
      <span class="wordmark__main">KORU</span>
      <span class="wordmark__sub">REAL ESTATE HOLDINGS LLC</span>
    </span>
  </div>

  <div class="address">
    <svg class="icon" viewBox="0 0 12 12" style="width:13px;height:16px;margin-top:2px"><path d="M6 0a4.5 4.5 0 0 0-4.5 4.5C1.5 8 6 12 6 12s4.5-4 4.5-7.5A4.5 4.5 0 0 0 6 0zm0 6.3a1.8 1.8 0 1 1 0-3.6 1.8 1.8 0 0 1 0 3.6z"/></svg>
    <div>214 9th floor,Plaza<br>Harbor Street DCA</div>
  </div>

  <span class="band band--side"></span>
  <div class="person">
    <p class="person__name">DANIEL MERCER</p>
    <p class="person__role">Managing Director</p>
  </div>

  <ul class="contacts">
    <li><svg class="icon" viewBox="0 0 12 12"><path d="M2.5 0.5l2 2.5-1 1.3c.7 1.6 2 2.9 3.6 3.6l1.3-1 2.5 2-1.2 2.1C5 10.8 1.2 7 .4 1.7z"/></svg>012 555 0148</li>
    <li><svg class="icon" viewBox="0 0 12 12"><path d="M3 0h6v12H3zM4 1.5v8h4v-8z"/></svg>012 555 0148</li>
    <li><svg class="icon" viewBox="0 0 12 12"><path d="M0 3h12v7H0zM0.8 3.6L6 7.5l5.2-3.9"/></svg>012 555 0148</li>
    <li><svg class="icon" viewBox="0 0 12 12"><path d="M0 2h12v8H0zM1 3l5 3.6L11 3v-.2H1z" fill-rule="evenodd"/></svg>info@koruhold.com</li>
    <li><svg class="icon" viewBox="0 0 12 12"><circle cx="6" cy="6" r="5.5" fill="none" stroke="#3a3a3c"/><path d="M.5 6h11M6 .5c-3 3-3 8 0 11M6 .5c3 3 3 8 0 11" fill="none" stroke="#3a3a3c"/></svg>www.koruholdings.com</li>
  </ul>
</section>

</body>
</html>
```